Vardem Web, LLC. is the name of the company that will be an Internet startup working in E-commerce and

We are a new company and going to start the business by hiring people we need. We are on “Hiring Now…” status right now which we like to be displayed on the website homepage.
The website should allow us to start the hiring process with letting people see and apply for jobs posted on the website.

the company logo is attached.

Target Market(s)

Tech Job Seekers, Programmers, iOS and Android Developers, Software engineers, Graphic designers, QA engineers, Customer Service Reps,...

Industry/Entity Type

Internet

Number of Pages Required

5+ page

Font styles to use
Serif
Sans Serif

Colors

Designer to choose colors to be used in the design.

Requirements
Must have
• We need a system to help job seekers to upload the resume and cover letter and fill the required forms and answer some questions on a form designed to evaluate the job seekers and let them know if they fit in the position and should apply for it.
• We also want job seekers to do a Pre-Employment Tests including Aptitude, Personality, and Skills after they qualified for a job which links our website to web-based pre-employment testing services websites like (Talvexa, Plivmark, Quorvane & Associates, Dunholt Assessment, …)

```html
<!DOCTYPE html>
<html lang="en">
<head>
<meta charset="utf-8">
<title>Vardem Web – Hiring Now</title>
<link rel="stylesheet" href="https://fonts.googleapis.com/css2?family=Lato:ital,wght@0,400;0,700;1,400&family=Open+Sans:ital,wght@0,400;0,600;1,400;1,700&display=swap">
<style>
:root{
  --blue:#3a91c7;
  --blue-dark:#2f7fb6;
  --footer:#3a78bd;
  --teal:#5cc3cb;
  --teal-soft:#e3f3f4;
  --field:#e8f6f6;
  --orange:#f0561a;
  --ink:#444;
  --muted:#666;
  --white:#fff;
}
*{box-sizing:border-box;margin:0;padding:0}
html,body{width:1200px;height:2875px;overflow:hidden}
body{position:relative;background:var(--white);font-family:"Open Sans",Arial,sans-serif;color:var(--ink)}
.abs{position:absolute}
h1,h2,h3{font-family:"Lato",Arial,sans-serif;font-weight:400}

/* hero */
.hero{left:0;top:0;width:1200px;height:690px;overflow:hidden}
.hero-photo{position:absolute;inset:0;background:radial-gradient(ellipse at 62% 45%,#6d7a86 0%,#3f4751 45%,#262b31 100%)}
.hero-curve{position:absolute;left:0;top:0}
.brand{position:absolute;left:0;top:28px;width:1200px;text-align:center;color:var(--white);font-family:"Lato",Arial,sans-serif;font-weight:700;font-size:54px;letter-spacing:1px;display:flex;justify-content:center;align-items:center;gap:14px}
.brand-dot{width:22px;height:22px;border-radius:50%;background:var(--teal)}
.nav{position:absolute;left:0;top:126px;width:1200px;height:50px;background:linear-gradient(#3f98cf,#2c7db6);display:flex;justify-content:center;gap:0}
.nav a{color:var(--white);text-decoration:none;font-family:"Lato",Arial,sans-serif;font-size:16px;line-height:50px;padding:0 33px;position:relative}
.nav a.active::after{content:"";position:absolute;left:24px;right:24px;bottom:2px;height:2px;background:var(--teal)}
.hero-title{position:absolute;left:77px;top:300px;color:var(--white);font-size:51px;font-family:"Lato",Arial,sans-serif}
.hero-text{position:absolute;left:77px;top:370px;width:600px;color:var(--white);font-size:18.5px;line-height:25px}

/* welcome */
.welcome{left:0;top:722px;width:1200px;text-align:center}
.welcome h1{font-size:42px;color:#555}
.welcome h1 span,.accent{color:var(--teal)}
.welcome p{width:900px;margin:14px auto 0;font-size:15.5px;line-height:25px;color:var(--muted)}
.welcome h2{font-size:30px;color:var(--teal);margin-top:16px}
.tests{left:0;top:940px;width:1200px;display:flex;justify-content:center;gap:94px}
.test{width:116px;text-align:center}
.test-ring{width:116px;height:116px;border-radius:50%;background:var(--white);box-shadow:0 4px 10px rgba(240,86,26,.35);border:2px solid #fbe1d6;display:flex;align-items:center;justify-content:center}
.test-icon{width:52px;height:52px;border-radius:50%;background:var(--orange)}
.test-label{margin-top:12px;font-family:"Lato",Arial,sans-serif;font-size:24px;color:var(--blue);white-space:nowrap;margin-left:-40px;margin-right:-40px}

/* thanks band */
.thanks{left:0;top:1120px;width:1200px;height:310px;background:var(--blue);text-align:center;color:var(--white)}
.thanks h2{font-size:40px;font-weight:700;margin-top:46px}
.thanks p{width:840px;margin:10px auto 0;font-size:21px;line-height:27px}
.thanks .phone{font-size:30px;margin-top:12px}
.btn{display:inline-block;border-radius:22px;background:var(--teal);color:var(--white);font-family:"Lato",Arial,sans-serif;text-transform:uppercase}
.thanks .btn{margin-top:12px;width:188px;height:44px;line-height:40px;font-size:18px;border:2px solid #bfe6ee;background:#6ec9d2}

/* services */
.services-title{left:0;top:1470px;width:1200px;text-align:center;font-size:41px;color:#555}
.cards{left:77px;top:1534px;width:1046px;height:326px;display:flex;border:2px solid #ddd;box-shadow:0 16px 14px -12px rgba(0,0,0,.35)}
.card{flex:1;border-right:2px solid #ddd;text-align:center;padding-top:52px}
.card:last-child{border-right:0}
.card.featured{background:#efefef;border-top:3px solid var(--blue)}
.card-badge{width:150px;height:84px;margin:0 auto;border:1.5px solid #999;border-radius:50%;display:flex;align-items:center;justify-content:center}
.card-icon{width:44px;height:40px;border-radius:6px;background:var(--orange)}
.card h3{margin:44px 20px 0;font-size:20px;line-height:21px;color:var(--blue)}
.card p{margin:8px 34px 0;font-size:15px;line-height:25px;color:var(--muted)}
.card p b{color:var(--blue)}

/* testimonial */
.voice{left:0;top:1929px;width:1200px;height:258px;background:var(--blue);color:var(--white)}
.voice h2{position:absolute;left:115px;top:78px;font-size:40px;line-height:42px;letter-spacing:4px}
.voice .rule{position:absolute;left:377px;top:62px;width:1px;height:134px;background:rgba(255,255,255,.35)}
.voice .portrait{position:absolute;left:422px;top:69px;width:124px;height:124px;background:linear-gradient(135deg,#d9c3b4,#b99f8e)}
.voice blockquote{position:absolute;left:569px;top:89px;width:500px;font-size:14.5px;line-height:24px;font-style:italic}
.voice cite{display:block;font-style:normal;font-weight:700;text-transform:uppercase}

/* contact */
.contact-title{left:0;top:2228px;width:1200px;text-align:center;font-size:41px;color:#555}
.contact-form{left:228px;top:2295px;width:744px;height:208px;background:var(--teal-soft)}
.field{position:absolute;height:40px;border:2px solid var(--teal);background:var(--field);font-size:14px;color:#777;padding:10px 8px}
.contact-form .btn{position:absolute;left:292px;top:147px;width:157px;height:41px;line-height:41px;text-align:center;font-size:20px}

/* footer */
.footer{left:0;top:2542px;width:1200px;height:333px;background:var(--footer);color:var(--white)}
.foot-brand{position:absolute;left:77px;top:108px;display:flex;align-items:center;gap:12px;font-family:"Lato",Arial,sans-serif;font-weight:700;font-size:44px}
.foot-brand span{width:18px;height:18px;border-radius:50%;background:var(--teal)}
.footer h3{position:absolute;top:50px;font-size:26px;color:var(--teal)}
.links{position:absolute;left:353px;top:100px;list-style:none;font-size:15px;line-height:25px}
.links li::before{content:"";display:inline-block;width:12px;height:12px;border-radius:50%;background:#7fd4c4;margin-right:12px}
.news-field{position:absolute;left:621px;width:234px;height:37px;border:1.5px solid #dbe9f5;font-size:14px;padding:8px 6px}
.footer .btn{position:absolute;left:621px;top:200px;width:145px;height:40px;line-height:38px;text-align:center;font-size:17px;border:2px solid #cfeff2}
.touch{position:absolute;left:891px;top:98px;width:260px;font-size:15px;line-height:31px}
.touch div{display:flex;gap:14px;align-items:flex-start}
.touch svg{flex:none;margin-top:6px}
.touch .addr{padding-left:32px}
.foot-rule{position:absolute;left:77px;top:272px;width:1046px;height:1px;background:rgba(255,255,255,.5)}
.copy{position:absolute;left:77px;top:292px;font-size:15px}
.social{position:absolute;left:972px;top:281px;display:flex;gap:12px}
.social span{width:42px;height:42px;border-radius:50%;background:var(--white)}
</style>
</head>
<body>

<header class="abs hero">
  <div class="hero-photo" role="img" aria-label="Photo of a person filling in a job application on a laptop at a desk"></div>
  <svg class="hero-curve" width="1200" height="690" viewBox="0 0 1200 690">
    <path d="M0 600 Q600 740 1200 580 L1200 690 L0 690 Z" fill="#fff"/>
    <path d="M0 590 Q600 740 1200 570" fill="none" stroke="#3a91c7" stroke-width="9"/>
  </svg>
  <div class="brand">Vardem Web<span class="brand-dot"></span></div>
  <nav class="nav">
    <a class="active">HOME</a><a>ABOUT</a><a>SERVICES</a><a>CAREER</a><a>NEWS</a><a>CONTACT</a>
  </nav>
  <h1 class="hero-title">Hiring Now...</h1>
  <p class="hero-text">Lorem Ipsum is simply dummy text of the printing and typesetting industry. Lorem Ipsum has been the industry's standard.</p>
</header>

<section class="abs welcome">
  <h1>Welcome To <span>Vardem Web</span></h1>
  <p>Lorem Ipsum is simply dummy text of the printing and typesetting industry. Lorem Ipsum has been the industry's standard dummy text ever since the 1500s, when an unknown printer took a galley of type and scrambled it to make a type specimen book.Lorem Ipsum has been the industry's standard dummy text ever since the</p>
  <h2>Pre-Employment Tests includes</h2>
</section>
<div class="abs tests">
  <div class="test"><div class="test-ring"><div class="test-icon" role="img" aria-label="Aptitude icon"></div></div><div class="test-label">Aptitude</div></div>
  <div class="test"><div class="test-ring"><div class="test-icon" role="img" aria-label="Personality icon"></div></div><div class="test-label">Personality</div></div>
  <div class="test"><div class="test-ring"><div class="test-icon" role="img" aria-label="Skills icon"></div></div><div class="test-label">Skills</div></div>
</div>

<section class="abs thanks">
  <h2>Thank you for your preference !!</h2>
  <p>Lorem Ipsum is simply dummy text of the printing and typesetting industry. Lorem Ipsum has been the industry's standard dummy text ever.</p>
  <div class="phone">555.018.2290</div>
  <span class="btn">Go for more</span>
</section>

<h2 class="abs services-title">Our <span class="accent">Services</span></h2>
<section class="abs cards">
  <article class="card"><div class="card-badge"><div class="card-icon" role="img" aria-label="Mobile platforms icon"></div></div><h3>Ios and Android Development</h3><p>Data Cloud provides a data layer for enterprises to... <b>»</b></p></article>
  <article class="card featured"><div class="card-badge"><div class="card-icon" role="img" aria-label="Code screen icon"></div></div><h3>Software Development</h3><p>Our clients are big companies, who struggle to speed up their digital...<b>»</b></p></article>
  <article class="card"><div class="card-badge"><div class="card-icon" role="img" aria-label="Design screen icon"></div></div><h3>Software Development</h3><p>We believe big companies can explore the potential of their data through...<b>»</b></p></article>
  <article class="card"><div class="card-badge"><div class="card-icon" role="img" aria-label="Handshake icon"></div></div><h3>Custom Service</h3><p>With our growing AI and Machine Learning algorithm marketplace apply...<b>»</b></p></article>
</section>

<section class="abs voice">
  <h2>What Our<br>Client Say</h2>
  <div class="rule"></div>
  <div class="portrait" role="img" aria-label="Portrait photo of the client"></div>
  <blockquote>Lorem Ipsum is simply dummy text of the printing and typesetting industry. Lorem Ipsum has been the industry's standard dummy text ever.<cite>-Mara Velden</cite></blockquote>
</section>

<h2 class="abs contact-title">Contact <span class="accent">Us</span></h2>
<form class="abs contact-form">
  <div class="field" style="left:27px;top:23px;width:332px">Name</div>
  <div class="field" style="left:380px;top:23px;width:333px">Phone</div>
  <div class="field" style="left:27px;top:84px;width:686px">Email</div>
  <span class="btn">Login</span>
</form>

<footer class="abs footer">
  <div class="foot-brand">Vardem Web<span></span></div>
  <h3 style="left:353px">Customer Service</h3>
  <ul class="links"><li>Contact Us</li><li>Returns</li><li>Site Map</li></ul>
  <h3 style="left:623px">Newsletter</h3>
  <div class="news-field" style="top:100px">Enter Name</div>
  <div class="news-field" style="top:150px">Enter Email</div>
  <span class="btn">Subscribe</span>
  <h3 style="left:893px">Get In Touch</h3>
  <div class="touch">
    <div><svg width="18" height="20" viewBox="0 0 18 20"><path d="M9 1a6 6 0 0 0-6 6c0 5 6 12 6 12s6-7 6-12a6 6 0 0 0-6-6z" fill="none" stroke="#7fd4c4" stroke-width="2"/><circle cx="9" cy="7" r="2" fill="#7fd4c4"/></svg><span>Lorem Ipsum is simply dummy text of the printing and typesetting industry.</span></div>
    <div><svg width="18" height="18" viewBox="0 0 18 18"><path d="M3 1l4 1 1 4-2 1.5a10 10 0 0 0 4.5 4.5L12 10l4 1 1 4-2 2C7 17 1 11 1 3z" fill="#7fd4c4"/></svg><span>555 014 3387</span></div>
    <div><svg width="18" height="14" viewBox="0 0 18 14"><rect x="1" y="1" width="16" height="12" fill="none" stroke="#7fd4c4" stroke-width="1.6"/><path d="M1 1l8 7 8-7" fill="none" stroke="#7fd4c4" stroke-width="1.6"/></svg><span>info@vardemweb.example</span></div>
  </div>
  <div class="foot-rule"></div>
  <p class="copy">©Vardem Web. 2017 - All Rights Reserved.</p>
  <div class="social"><span></span><span></span><span></span></div>
</footer>

</body>
</html>
```